Systems and Technology Consultants - Website

Design & Build a website for a new company which operates in the Systems and Technology space for Transportation, Government and Commercial sectors.

Overall design should be minimalist in nature.
Should also have a feed that provides news and event updates on the main page.
Logo has already been awarded and should be incorporated into the site.

We like the overall layout, functionality and simplicity of the below sites. Submitted designs could be similar to or a combination of the aspects on these sites, or perhaps a whole different concept - we are open to new ideas.
Norvique.com
Teblo.it

Update 1 Dated 27 May 2014

All I am moving away from the Teblo.it website and would like it to be more aligned with Norvique.com not only in layout but in functionality. I will be extending the deadline of this design brief for two weeks to incorporate additional requirements and will add addtional funding to the project.

Apologies for not having more information available to provide but with so many submissions its getting confusing.

Thanks Derek

Please note that the brief has been updated and the deadline has been extended.

Important: We will need two language versions of the website, English and Arabic; the website is hosted on HostPelican

Hello All, Thank you for your submissions. We have narrowed it down to the final 6 designers and I just wanted to take a moment and provide a bit of feedback regarding the concepts that we like and the modifications we are looking for. First, let me mention some of the design functions we like. - At the top of the homepage we really like the "region" or "language" tab so that the website can be viewed in both English and Arabic. - We like the homepage to have clear color variation so that the different sections of the homepage are distinct. Additionally, we like the bottom portion of the homepage to be in red. We feel that draws attention to our contact information. Again, we would like the colors to integrate black, gray-scale, red, etc. - Having a search tab at the top of the home page, or integrated into the main image, so that the site is easy to navigate. - We especially like the main image to have the scrolling tabs at the bottom so it is easy to browse the services offered (Consultancy, Solutions Architecture, Masters Systems Integration, Independent Design Review). - In regards to the services offered tab we really like the idea that a few people presented that have the outside of our logo with an icon in the middle of consultancy, solutions, etc., etc. Secondly, as mentioned in our brief we really enjoy the design of norvique site. Specially, we enjoy the strong iconic images they use, the way the tabs at the top scroll easily, and contact us page that generates an email. Lastly, I've included some photos of the concept we have been working on. What we are trying to demonstrate is how our company offers a range of services that are essentially linked together. We provide individual services that when combined present the full service package. We would like this concept to be integrated into the over concept of our website. Please feel free to ask for clarification of any of the above points or contact us if you have any additional questions. We appreciate all of your hard work and are very excited to see the updated designs. Best, Marta Vennick Quelbrant Senior Program Manager marta.vennick@quelbrant-example.com

Industry/Entity Type

Government

Font styles to use
Serif
Sans Serif

Requirements
Must have
• Must work on/adapt to various/mobile devices (responsive)
Must be simple and straightforward
Colors should be in line/matching with logo
2 language versions: English and Arabic (no Thai)
Services should be the first group/row of items after/below the main image
Note: the website will be hosted by hostpelican
Nice to have
• Submit feedback form
What's New section
The banner at the bottom of the site should not be too large; we would like a narrow one more
It would be nice if the header/top banner (with Home, About, etc. tabs) could stay in place as you scroll down (like Norvique and Chatterloop)
We will likely only use one image with a Company slogan on the Home page rather than a carousel of images to rotate through
Should not have
• This is the existing website: http://www.quelbrant-example.org
We do not like the animation, the way the banner icons/titles bounce
Not simple enough, we don't like the functionality or how pages load so slowly
We do not like the logo centered - it should be at the left
The banner and its tabs should not be towards the right, we would like them to be centered, to go all the way across and to be below the logo

```html
<!DOCTYPE html>
<html lang="en">
<head>
<meta charset="utf-8">
<title>Quelbrant Group</title>
<link href="https://fonts.googleapis.com/css2?family=Open+Sans:wght@400;600&display=swap" rel="stylesheet">
<style>
:root{
  --red:#c9000b;
  --red-text:#cc1111;
  --ink:#222;
  --muted:#666;
  --light:#f0f0f0;
  --card:#e6e6e6;
  --footer:#232323;
  --footer-text:#b5b5b5;
}
*{box-sizing:border-box;margin:0;padding:0}
html,body{width:1176px;height:1200px;overflow:hidden;background:#fff;font-family:"Open Sans",Arial,sans-serif;color:var(--ink)}
.page{position:relative;width:1176px;height:1200px}
.top-band{position:absolute;left:0;top:0;width:1176px;height:147px;background:var(--light);border-top:3px solid #111}
.brand{position:absolute;left:110px;top:60px;display:flex;align-items:center;gap:8px;font-size:18px;font-weight:600;color:var(--red);letter-spacing:3px}
.brand-mark{width:14px;height:14px;background:var(--red)}
.social{position:absolute;left:962px;top:47px;display:flex;gap:5px}
.social span{width:32px;height:32px;border-radius:3px}
.s-blue{background:#3a66b0}.s-orange{background:#f39a1e}.s-sky{background:#4fb0e6}
.nav{position:absolute;left:108px;top:127px;width:960px;height:41px;background:var(--red);border-radius:4px;display:flex;align-items:center;padding-left:14px}
.nav a{color:#fff;text-decoration:none;font-size:13px;margin-right:43px;text-transform:uppercase}
.nav a.active{background:#fff;color:var(--red);padding:4px 10px;border-radius:2px;margin-right:33px}
.search{position:absolute;right:10px;top:10px;width:218px;height:22px;background:#fff;border-radius:2px}
.search svg{position:absolute;right:5px;top:4px}
.hero{position:absolute;left:108px;top:184px;width:960px;height:311px;background:linear-gradient(90deg,#e6eef2 0%,#b9cfdb 45%,#6f8ea6 62%,#3a4f64 80%,#6f7d88 100%);border:1px solid #ddd}
.hero-shadow{position:absolute;left:118px;top:495px;width:960px;height:40px;background:radial-gradient(ellipse at top,rgba(0,0,0,.45),rgba(0,0,0,0) 70%)}
.hero-box{position:absolute;left:108px;top:258px;width:428px;height:169px;background:rgba(20,20,20,.9);border-radius:0 3px 3px 0;padding:18px 12px 0 37px;color:#fff}
.hero-box h1{font-weight:400;font-size:35px;letter-spacing:-1px;margin-bottom:12px}
.hero-box p{font-size:14px;line-height:19px}
.cards{position:absolute;left:105px;top:569px;display:flex;gap:6px}
.card{width:237px;height:209px;background:var(--card);border-radius:6px;overflow:hidden;position:relative;box-shadow:0 12px 10px -10px rgba(0,0,0,.25)}
.card-img{height:102px}
.card-label{position:absolute;left:0;top:92px;width:190px;height:26px;background:#fff;clip-path:polygon(0 0,176px 0,190px 26px,0 26px);font-size:12px;padding:6px 0 0 15px}
.card p{position:absolute;left:16px;top:136px;width:210px;font-size:12.5px;line-height:16px;color:var(--muted)}
.img-red{background:var(--red);display:flex;align-items:center;justify-content:center;gap:8px;color:#fff;font-size:16px;font-weight:600;letter-spacing:3px}
.img-red i{width:12px;height:12px;background:#fff}
.img-build{background:linear-gradient(160deg,#4a6c9a,#9aa8b4 60%,#b8804a)}
.img-eng{background:linear-gradient(160deg,#5a6f86,#a9b6c2 50%,#2c3f66)}
.img-cons{background:linear-gradient(160deg,#e8eef4,#9fb6cc 50%,#3b3f48)}
.info{position:absolute;left:110px;top:847px;width:959px;height:246px;background:#f3f3f3;border:1px solid #eee}
.info h2{font-weight:400;font-size:20px;color:var(--red-text)}
.articles-img{position:absolute;left:15px;top:15px;width:142px;height:101px;background:linear-gradient(160deg,#1c2240,#6a5a4a 60%,#d8c79a)}
.articles-title{position:absolute;left:168px;top:16px}
.articles-lead{position:absolute;left:168px;top:48px;width:335px;font-size:12px;line-height:15px;color:var(--muted)}
.articles-body{position:absolute;left:15px;top:152px;width:500px;font-size:12px;line-height:15px;color:var(--muted)}
.read-more{position:absolute;left:15px;top:208px;font-size:12px;color:var(--red-text)}
.divider{position:absolute;left:520px;top:16px;width:1px;height:216px;background:#bbb}
.news{position:absolute;left:540px;top:16px;width:370px}
.news h3{font-weight:400;font-size:15px;margin:10px 0 3px 4px}
.news p{font-size:10.5px;line-height:18px;margin-left:4px}
.news .row{display:flex;justify-content:space-between;font-size:10.5px;margin-left:4px}
.news .date{color:#999}
.footer{position:absolute;left:0;top:1143px;width:1176px;height:57px;background:var(--footer);color:var(--footer-text);font-size:12px}
.footer-links{position:absolute;left:112px;top:23px;display:flex;gap:20px}
.footer-copy{position:absolute;left:848px;top:24px}
</style>
</head>
<body>
<div class="page">
  <div class="top-band"></div>
  <div class="brand"><span class="brand-mark"></span>QUELBRANT</div>
  <div class="social"><span class="s-blue"></span><span class="s-orange"></span><span class="s-sky"></span></div>

  <nav class="nav">
    <a class="active">Home</a><a>Business Unit</a><a>Services</a><a>About Us</a><a>Locations</a><a>Contact Us</a>
    <div class="search"><svg width="14" height="14" viewBox="0 0 14 14"><circle cx="6" cy="6" r="4.5" fill="none" stroke="#111" stroke-width="2"/><line x1="9.3" y1="9.3" x2="13" y2="13" stroke="#111" stroke-width="2"/></svg></div>
  </nav>

  <div class="hero" role="img" aria-label="Engineer in a hard hat holding rolled plans, team meeting in an office behind"></div>
  <div class="hero-shadow"></div>
  <div class="hero-box">
    <h1>Quelbrant Group</h1>
    <p>quelbrant specializes in delivering quality professional services and technical projects that support larger business goals.&nbsp; systems are tools that support a greater business function and need.</p>
  </div>

  <div class="cards">
    <div class="card"><div class="card-img img-red"><i></i>QUELBRANT</div><div class="card-label">ABOUT US</div><p>It is a long established fact that a reader will be distracted by the read-able content of a page when looking</p></div>
    <div class="card"><div class="card-img img-build" role="img" aria-label="Construction workers on a steel frame site"></div><div class="card-label">CONSTRUCTION</div><p>It is a long established fact that a reader will be distracted by the read-able content of a page when looking</p></div>
    <div class="card"><div class="card-img img-eng" role="img" aria-label="Engineer working at a control panel"></div><div class="card-label">ENGINEERING</div><p>It is a long established fact that a reader will be distracted by the read-able content of a page when looking</p></div>
    <div class="card"><div class="card-img img-cons" role="img" aria-label="Consultants meeting before a chart screen"></div><div class="card-label">CONSULTING</div><p>It is a long established fact that a reader will be distracted by the read-able content of a page when looking</p></div>
  </div>

  <section class="info">
    <div class="articles-img" role="img" aria-label="Hotel terrace at night"></div>
    <h2 class="articles-title">Our Articles</h2>
    <p class="articles-lead">It is a long established fact that a reader will be distracted by the readable content of a page when looking at its layout. The point of using Lorem Ipsum is that it has a more-or-less normal distribution of letters, as opposed to using 'Content here, content here</p>
    <p class="articles-body">It is a long established fact that a reader will be distracted by the readable content of a page when looking at its layout. The point of using Lorem Ipsum is that it has a more-or-less normal distribution of letters, as opposed to using 'Content here, content here</p>
    <a class="read-more">Read More</a>
    <div class="divider"></div>
    <div class="news">
      <h2>Our News</h2>
      <h3>Investing In Real Estate</h3>
      <p>New terminal opens at Kestrel Field Airport</p>
      <p>August 15, 2013 Concessionaire in Bulgaria's Velmont..</p>
      <div class="row"><span>Read More....</span><span class="date">› May 25. February 2013</span></div>
      <h3 style="margin-top:22px">Current Projects</h3>
      <p>Concessionaire in Bulgaria's Velmont..</p>
      <p>Resort to Expand Ski Runs Bulgaria's Best for a Cheap Trip.</p>
      <div class="row"><span>Read More...</span><span class="date">› May 25. February 2013</span></div>
    </div>
  </section>

  <footer class="footer">
    <div class="footer-links"><span>Home</span><span>|</span><span>Business Units</span><span>|</span><span>Services</span><span>|</span><span>About Us</span><span>|</span><span>Locations</span><span>|</span><span>Contact Us</span></div>
    <div class="footer-copy">©2004 quelbrant. |&nbsp;&nbsp; All rights reserved.</div>
  </footer>
</div>
</body>
</html>
```